Redesign a Start-Up Dating Website

Website: https://morvelique.com.
Make sure the design has an island style theme.
I would like the 7 pages of my website to have a new and professional look. I want the same colors to remain, but I want a creative look for all the pages. This is a dating website that is in the startup stage. So, I want to give my entire website a custom makeover. I want something that will stand out from the other dating sites. Something that will attract more people to want to use my services, and hopefully get new members.
Target Market(s)
Dating
Industry/Entity Type
Dating
Coding
Coded - Design and coding required
Number of Pages Required
5+ page
Font styles to use
Other font styles liked:
- Decorative, San Serif
Requirements
Must have
- The design must have the original colors and a stylish font to go along. The design must be creative, welcoming, and professional. I would like an island style theme for the website. This is a dating website so make sure that the design is tailored to that aspect.
Nice to have
- It would be nice to have a decorative font and a professional style on all the pages. Make sure the design will be mobile responsive and friendly for all the pages on the website.
Should not have
- The design should not be bland and uncreative.

```html
<!DOCTYPE html>
<html lang="en">
<head>
<meta charset="utf-8">
<title>Morvelique – Choose your soul mate</title>
<link rel="stylesheet" href="https://fonts.googleapis.com/css2?family=Playball&family=Raleway:wght@400;500;600;700&display=swap">
<style>
:root{
  --orange:#f7a21b;
  --orange-dark:#e8900c;
  --teal:#1fb7ad;
  --teal-deep:#128f8a;
  --teal-soft:#5fd0c6;
  --script-green:#2bb79a;
  --purple:#7b3d8e;
  --ink:#555;
  --white:#fff;
  --sky:#3d8fd2;
}
*{box-sizing:border-box;margin:0;padding:0}
html,body{width:1200px;height:3673px;overflow:hidden}
body{position:relative;font-family:"Raleway",sans-serif;color:var(--ink);background:var(--white)}
.abs{position:absolute}
.script{font-family:"Playball",cursive;font-weight:400}
.btn{position:absolute;display:flex;align-items:center;justify-content:center;background:var(--orange);color:var(--white);border-radius:40px;font-family:"Playball",cursive;font-size:28px;white-space:nowrap;box-shadow:0 4px 8px rgba(0,0,0,.15)}
.photo{position:absolute}

/* hero */
.hero{position:absolute;left:0;top:0;width:1200px;height:690px;clip-path:polygon(0 0,100% 0,100% 78%,0 100%);
  background:linear-gradient(180deg,#2f7fcf 0%,#7ab9ea 38%,#bfe1f4 48%,#2a9fc4 56%,#1b7fa8 75%,#d9c7a3 100%)}
.hero-couple{left:760px;top:60px;width:440px;height:560px;background:radial-gradient(ellipse at 55% 45%,#f4f4f4 0%,#d9d3cb 45%,rgba(80,60,50,.55) 75%,rgba(0,0,0,0) 100%)}
.brand{position:absolute;left:73px;top:20px;display:flex;align-items:center;gap:14px}
.brand-dot{width:74px;height:74px;border-radius:50%;background:var(--orange)}
.brand-name{font-family:"Raleway",sans-serif;font-weight:700;font-size:46px;color:var(--white)}
.nav{position:absolute;right:78px;top:58px;display:flex;gap:32px;font-size:16px;font-weight:500;color:var(--white)}
.nav .active{color:var(--orange)}
.auth{position:absolute;top:8px;height:42px;border-radius:21px;background:var(--orange);color:var(--white);display:flex;align-items:center;gap:8px;padding:0 18px;font-size:15px;font-weight:600}
.hero-title{left:78px;top:236px;font-size:64px;color:var(--white);white-space:nowrap;text-shadow:0 3px 8px rgba(0,0,0,.35)}
.hero-line{left:80px;font-size:21px;font-weight:700;font-style:italic;color:var(--white);white-space:nowrap;text-shadow:0 2px 5px rgba(0,0,0,.35)}
.hero-line em{color:var(--orange)}

/* welcome */
.welcome-box{left:159px;top:727px;width:510px;height:270px;border:4px solid var(--orange);background:var(--white);padding:24px 30px;z-index:2}
.welcome-box h2{font-family:"Playball",cursive;font-weight:400;font-size:34px;color:var(--script-green);margin-bottom:12px}
.welcome-box p{font-size:13px;line-height:1.75}

/* steps band */
.band{position:absolute;left:0;width:1200px;background:linear-gradient(135deg,#27bfb4,#158f8f 55%,#23a9a5)}
.steps{top:1170px;height:593px;clip-path:polygon(0 0,100% 22%,100% 100%,0 100%)}
.step{position:absolute;top:1385px;width:360px;text-align:center;color:var(--white)}
.step h3{font-family:"Playball",cursive;font-weight:400;font-size:36px;margin:14px 0 12px}
.step p{font-size:14px;line-height:1.6;padding:0 14px}
.step .arrow{margin-top:18px}

/* community */
.comm-title{left:470px;top:1830px;width:620px;text-align:center;font-size:34px;color:var(--script-green);white-space:nowrap}
.member{position:absolute;top:1922px;width:162px;height:162px;border-radius:50%;border:3px solid var(--teal-soft);padding:8px}
.member span{display:block;width:100%;height:100%;border-radius:50%}
.comm-text{left:480px;width:600px;text-align:center;font-size:14px;font-weight:600;text-transform:uppercase;color:#333;white-space:nowrap}
.comm-text em{color:var(--orange);font-style:normal;text-decoration:underline}

/* benefits */
.benefits{top:2300px;height:467px;clip-path:polygon(0 24%,100% 0,100% 100%,0 100%)}

/* search */
.search-bg{left:0;top:2767px;width:1200px;height:613px;background:linear-gradient(180deg,#eef0f2,#f8f8f9 40%,#eceeef)}
.label{position:absolute;font-size:14px;font-weight:600;color:#444}
.field{position:absolute;height:44px;border:1px solid #d5d5d5;border-radius:22px;background:var(--white);display:flex;align-items:center;justify-content:space-between;padding:0 16px;font-size:13px;color:#999}
.field::after{content:"";border:7px solid transparent;border-top:8px solid #777;margin-top:8px}

/* footer */
.footer{left:0;top:3380px;width:1200px;height:293px;background:var(--teal)}
.foot-badge{left:525px;top:3305px;width:150px;height:150px;border-radius:50%;background:var(--white);border:6px solid var(--teal-soft);display:flex;align-items:center;justify-content:center;font-weight:700;font-size:21px;color:var(--orange)}
.social{position:absolute;top:3478px;width:58px;height:58px;border-radius:50%;background:var(--white);display:flex;align-items:center;justify-content:center}
.social span{width:42px;height:42px;border-radius:50%;background:#1e4f8f}
.foot-nav{left:0;top:3568px;width:1200px;display:flex;justify-content:center;font-size:15px;color:var(--white)}
.foot-nav span{padding:0 18px;border-left:1px solid rgba(255,255,255,.7)}
.foot-nav span:first-child{border-left:0;font-weight:700}
.copy{left:0;top:3606px;width:1200px;text-align:center;font-size:14px;color:var(--white)}
</style>
</head>
<body>

<!-- Hero -->
<section class="hero" role="img" aria-label="Tropical beach with turquoise sea, rope fence and palm trees"></section>
<div class="photo hero-couple" role="img" aria-label="Happy couple dancing on the beach"></div>
<div class="brand"><span class="brand-dot"></span><span class="brand-name">Morvelique</span></div>
<div class="auth" style="left:910px">
  <svg width="16" height="16" viewBox="0 0 16 16"><circle cx="8" cy="5" r="4" fill="#fff"/><path d="M1 16c0-5 14-5 14 0z" fill="#fff"/></svg>Login</div>
<div class="auth" style="left:1008px">
  <svg width="16" height="16" viewBox="0 0 16 16"><rect x="2" y="1" width="12" height="14" rx="2" fill="none" stroke="#fff" stroke-width="2"/><path d="M5 8h6" stroke="#fff" stroke-width="2"/></svg>Register</div>
<nav class="nav"><span class="active">HOME</span><span>SEARCH</span><span>MEMBERS</span><span>EXTRAS</span><span>ABOUT</span><span>PREMIUM</span><span>CONTACT</span></nav>
<h1 class="abs script hero-title">Choose your soul mate</h1>
<p class="abs hero-line" style="top:338px">Let's find your perfect match <em>today</em></p>
<p class="abs hero-line" style="top:380px">Find your perfect Match for <em>Free!</em></p>
<p class="abs hero-line" style="top:422px">Online dating made easy on <em>morvelique.com</em></p>
<div class="btn" style="left:78px;top:474px;width:208px;height:58px">Join Us Free</div>

<!-- Welcome -->
<div class="abs welcome-box">
  <h2>Welcome To Morvelique</h2>
  <p>Morvelique aims to provide a straight-forward, easy-to-use online dating service. I won't over-complicate things or reduce the amount of people you can talk to with algorithms. I know that sometimes, opposites attract and sparks can fly with the last person you thought you'd be interested in-so I won't hide anybody from you.There is no discrimination on this dating site, it's not only.</p>
</div>
<div class="btn" style="left:360px;top:1016px;width:206px;height:58px">Read More</div>
<div class="photo" role="img" aria-label="Couple embracing, woman on man's back" style="left:590px;top:686px;width:316px;height:338px;background:linear-gradient(160deg,#9fb8cc,#d7c3b2 60%,#e9e6e3)"></div>
<div class="photo" role="img" aria-label="Couple in winter hats" style="left:908px;top:870px;width:154px;height:154px;background:linear-gradient(160deg,#e8e4e2,#c9b8ae)"></div>
<div class="photo" role="img" aria-label="Couple kissing at sunset" style="left:590px;top:1028px;width:158px;height:154px;background:linear-gradient(160deg,#f0b07a,#6a4a3a)"></div>
<div class="photo" role="img" aria-label="Couple with balloons in a park" style="left:752px;top:1028px;width:154px;height:154px;background:linear-gradient(160deg,#b9c48a,#7a6a4e)"></div>
<div class="photo" role="img" aria-label="Smiling couple portrait" style="left:908px;top:1028px;width:154px;height:154px;background:linear-gradient(160deg,#e5ded5,#9b8574)"></div>
<div class="photo" role="img" aria-label="Couple under an umbrella" style="left:436px;top:1184px;width:154px;height:152px;background:linear-gradient(160deg,#7f9aa6,#c6cdcf)"></div>
<div class="photo" role="img" aria-label="Couple laughing together" style="left:590px;top:1184px;width:158px;height:152px;background:linear-gradient(160deg,#d6cfc6,#a88d79)"></div>
<div class="photo" role="img" aria-label="Couple close together outdoors" style="left:752px;top:1184px;width:154px;height:152px;background:linear-gradient(160deg,#b78a6a,#3c2e2a)"></div>

<!-- Steps -->
<section class="band steps" role="img" aria-label="Tropical coastline with cliffs and turquoise water, tinted teal"></section>
<div class="step" style="left:63px">
  <svg width="110" height="110" viewBox="0 0 110 110" fill="none" stroke="var(--purple)" stroke-width="5"><rect x="10" y="6" width="90" height="98" rx="10"/><circle cx="38" cy="40" r="11"/><path d="M20 72c2-14 34-14 36 0"/><path d="M64 36h24M64 52h24M20 86h68"/></svg>
  <h3>Create a Profile</h3>
  <p>Let people know all about you; the good and the quirky-show the world your true colors and find someone with the same unique qualities as you.</p>
  <div class="arrow"><svg width="34" height="12"><path d="M0 6h28M22 1l8 5-8 5" stroke="var(--orange)" stroke-width="3" fill="none"/></svg></div>
</div>
<div class="step" style="left:420px">
  <svg width="160" height="110" viewBox="0 0 160 110" fill="none" stroke="var(--purple)" stroke-width="5"><circle cx="55" cy="52" r="38"/><circle cx="108" cy="52" r="38"/><path d="M20 104h130"/></svg>
  <h3>Find Matches</h3>
  <p>Browse other users and feel the excitement of getting your first message and getting to know potential dates in a safe and fun environment.</p>
  <div class="arrow"><svg width="34" height="12"><path d="M0 6h28M22 1l8 5-8 5" stroke="var(--orange)" stroke-width="3" fill="none"/></svg></div>
</div>
<div class="step" style="left:785px">
  <svg width="120" height="110" viewBox="0 0 120 110" fill="none" stroke="var(--purple)" stroke-width="5"><circle cx="30" cy="24" r="11"/><circle cx="90" cy="24" r="11"/><path d="M14 100V54c0-10 32-10 32 0v46M74 100V54c0-10 32-10 32 0v46"/><path d="M60 30c-4-8-14-2-8 6l8 8 8-8c6-8-4-14-8-6z" fill="var(--purple)" stroke="none"/></svg>
  <h3>Start Dating</h3>
  <p>Once you've found your potential soulmate, it's time to meet up and say 'Hello' to the start of your journey together.</p>
  <div class="arrow"><svg width="34" height="12"><path d="M0 6h28M22 1l8 5-8 5" stroke="var(--orange)" stroke-width="3" fill="none"/></svg></div>
</div>

<!-- Community -->
<div class="photo" role="img" aria-label="Smiling couple holding a red heart balloon" style="left:0;top:1860px;width:430px;height:565px;background:radial-gradient(ellipse at 50% 45%,#e9d8cc 0%,#f3ece7 50%,#fff 80%)"></div>
<h2 class="abs script comm-title">Join This Community Of Morvelique Members</h2>
<svg class="abs" style="left:398px;top:1985px" width="20" height="40"><path d="M16 2L4 20l12 18" stroke="#ccc" stroke-width="2" fill="none"/></svg>
<svg class="abs" style="left:1150px;top:1985px" width="20" height="40"><path d="M4 2l12 18L4 38" stroke="#ccc" stroke-width="2" fill="none"/></svg>
<div class="member" style="left:470px"><span role="img" aria-label="Member photo" style="background:linear-gradient(160deg,#f2b25a,#c86a2a)"></span></div>
<div class="abs" style="left:492px;top:1990px;font-size:18px;color:#fff;font-weight:600">+63, Germany</div>
<div class="member" style="left:703px"><span role="img" aria-label="Member photo" style="background:linear-gradient(160deg,#8a6a4a,#3a2a22)"></span></div>
<div class="member" style="left:928px"><span role="img" aria-label="Member photo" style="background:linear-gradient(160deg,#c79a6e,#5a3a2a)"></span></div>
<p class="abs comm-text" style="top:2134px">Sign-up for a <em>30 days free trial</em></p>
<p class="abs comm-text" style="top:2160px">Enjoy all the benefits Morvelique has to offer with a full membership.</p>
<div class="btn" style="left:572px;top:2207px;width:460px;height:58px;font-size:25px">Start Morveliquing With Free Sign - Up</div>

<!-- Benefits -->
<section class="band benefits" role="img" aria-label="Couple walking on a long wooden bridge, tinted teal"></section>
<h2 class="abs script" style="left:0;top:2486px;width:1200px;text-align:center;font-size:36px;color:#fff">Morvelique Benefits</h2>
<p class="abs" style="left:0;top:2552px;width:1200px;text-align:center;font-size:18px;font-weight:600;font-style:italic;color:#fff">Affordable Easy Sign - Up And cancellation Processes</p>
<div class="btn" style="left:463px;top:2598px;width:274px;height:60px">View Membership Plan</div>

<!-- Search -->
<div class="abs search-bg" role="img" aria-label="Faded grid of member portraits"></div>
<div class="photo" role="img" aria-label="Couple in hat looking at a phone together" style="left:745px;top:2860px;width:455px;height:520px;background:linear-gradient(160deg,#e8ddd2,#8fb3d4 60%,#f2f2f2)"></div>
<h2 class="abs script" style="left:157px;top:2826px;font-size:36px;color:var(--script-green);white-space:nowrap">Let's Find Your Perfect Match Today</h2>
<span class="label" style="left:185px;top:2900px">I am :</span>
<div class="field" style="left:167px;top:2926px;width:433px"><span>Man</span></div>
<span class="label" style="left:185px;top:2984px">Seeking A :</span>
<div class="field" style="left:167px;top:3010px;width:433px"><span>Woman</span></div>
<span class="label" style="left:185px;top:3068px">Age :</span>
<span class="label" style="left:400px;top:3068px">To :</span>
<div class="field" style="left:167px;top:3090px;width:212px"><span>18</span></div>
<div class="field" style="left:385px;top:3090px;width:215px"><span>99</span></div>
<span class="label" style="left:185px;top:3148px">Country :</span>
<div class="field" style="left:167px;top:3172px;width:433px"><span>Afghanistan</span></div>
<div class="btn" style="left:304px;top:3226px;width:156px;height:54px">Search</div>

<!-- Footer -->
<footer class="abs footer"></footer>
<div class="abs foot-badge">Morvelique</div>
<div class="social" style="left:495px"><span></span></div>
<div class="social" style="left:568px"><span style="background:#1a9fd9"></span></div>
<div class="social" style="left:643px"><span style="background:#1570a8"></span></div>
<nav class="abs foot-nav"><span>HOME</span><span>SEARCH</span><span>MEMBERS</span><span>EXTRAS</span><span>ABOUT</span><span>PREMIUM</span><span>CONTACT</span></nav>
<p class="abs copy">© Morvelique - 2017 All rights reserved | Privacy Policy</p>

</body>
</html>
```